Business Cards for a law firm

Business cards for our law firm. Use our silhoette logo and OAK PARTNERS - check our website (www.oakpartners.example)

Contact Information for Business Card

our silhouette logo, OAK PARTNERS, 800-555-0147, Dorian Pemberton, dorian@oakpartners.example

Requirements
Must have
• our silhouette logo, OAK PARTNERS, 800-555-0147, Dorian Pemberton, dorian@oakpartners.example

```html
<!DOCTYPE html>
<html lang="en">
<head>
<meta charset="utf-8">
<title>Oak Partners — Business Cards</title>
<link rel="stylesheet" href="https://fonts.googleapis.com/css2?family=Cinzel:wght@600;700&family=Arimo:wght@400&display=swap">
<style>
  :root {
    --stage: #3b3b3d;
    --card-back: #2b2b2d;
    --card-back-pattern: #353537;
    --paper: #ffffff;
    --navy: #1b2f6b;
    --silver: #a4a6ad;
    --white: #ffffff;
  }
  * { margin: 0; padding: 0; box-sizing: border-box; }
  html, body { width: 1200px; height: 689px; overflow: hidden; background: var(--stage); }
  .canvas {
    position: relative; width: 1200px; height: 689px;
    display: flex; align-items: center; justify-content: center; gap: 50px;
  }
  .card {
    position: relative; width: 525px; height: 300px;
    border-radius: 18px; overflow: hidden;
    box-shadow: 0 14px 30px rgba(0,0,0,.35);
  }
  /* Back */
  .card-back { background: var(--card-back); }
  .back-pattern {
    position: absolute; inset: 0;
    background: linear-gradient(135deg, var(--card-back) 0%, var(--card-back-pattern) 100%);
  }
  .back-name {
    position: absolute; right: 34px; top: 42px;
    font-family: "Cinzel", serif; font-weight: 700; font-size: 15px;
    letter-spacing: 2px; color: var(--white);
  }
  /* Front */
  .card-front { background: var(--paper); }
  .front-swoosh { position: absolute; inset: 0; }
  .brand {
    position: absolute; left: 30px; top: 132px;
    display: flex; align-items: center; gap: 10px;
  }
  .brand-mark { width: 12px; height: 12px; border-radius: 50%; background: var(--navy); flex: none; }
  .brand-name {
    font-family: "Cinzel", serif; font-weight: 600; font-size: 21px;
    letter-spacing: 2px; color: var(--navy); white-space: nowrap;
  }
  .contact {
    position: absolute; right: 22px; top: 150px;
    font-family: "Arimo", sans-serif; font-size: 11px; line-height: 16px;
    color: var(--white); text-align: right; list-style: none;
  }
  .contact li { display: flex; justify-content: flex-end; align-items: center; gap: 7px; white-space: nowrap; }
  .contact svg { width: 10px; height: 10px; fill: var(--white); flex: none; }
  .person-name {
    position: absolute; right: 22px; top: 228px;
    font-family: "Cinzel", serif; font-weight: 700; font-size: 18px;
    letter-spacing: 1px; color: var(--white); white-space: nowrap;
  }
</style>
</head>
<body>
<main class="canvas">
  <section class="card card-back" aria-label="Card back">
    <div class="back-pattern" role="img" aria-label="Tone-on-tone repeated logo pattern"></div>
    <span class="back-name">OAK PARTNERS</span>
  </section>

  <section class="card card-front" aria-label="Card front">
    <svg class="front-swoosh" viewBox="0 0 525 300" preserveAspectRatio="none" aria-hidden="true">
      <path d="M300 0 C375 90 345 215 180 300 L525 300 L525 0 Z" fill="var(--silver)"/>
      <path d="M322 0 C392 95 358 220 192 300 L525 300 L525 0 Z" fill="var(--navy)"/>
    </svg>
    <div class="brand">
      <span class="brand-mark"></span>
      <span class="brand-name">OAK PARTNERS</span>
    </div>
    <ul class="contact">
      <li>800-555-0147
        <svg viewBox="0 0 24 24"><path d="M6.6 10.8a15.1 15.1 0 0 0 6.6 6.6l2.2-2.2a1 1 0 0 1 1-.25 11.4 11.4 0 0 0 3.6.57 1 1 0 0 1 1 1V20a1 1 0 0 1-1 1A17 17 0 0 1 3 4a1 1 0 0 1 1-1h3.5a1 1 0 0 1 1 1 11.4 11.4 0 0 0 .57 3.6 1 1 0 0 1-.25 1z"/></svg></li>
      <li>dorian@oakpartners.example
        <svg viewBox="0 0 24 24"><path d="M2 5h20v14H2z M3.5 6.5 12 13l8.5-6.5" fill="none" stroke="#fff" stroke-width="2"/></svg></li>
      <li>www.oakpartners.example
        <svg viewBox="0 0 24 24"><circle cx="12" cy="12" r="9" fill="none" stroke="#fff" stroke-width="2"/><path d="M3 12h18M12 3c3 3 3 15 0 18M12 3c-3 3-3 15 0 18" fill="none" stroke="#fff" stroke-width="1.6"/></svg></li>
    </ul>
    <span class="person-name">Dorian Pemberton</span>
  </section>
</main>
</body>
</html>
```